Lumbra Ember Oven Kitchen (restaurant)

Restaurant with a cool vibe.
We need a refresh of existing site. Appealing to a hip crowd of 25 or older age bracket (mid price to high small town). Constant changes food and cocktail menu. A vibing atmosphere with jazz funk hip music.
Must be able to scale for any device… phone/mobile device super important.
Instagram: @Lumbra.Bexwell
Website: lumbrabexwell.example

Target Market(s)

25-55 age group

Number of Pages Required

1 page

Font styles to use
Sans Serif

Requirements
Must have
• Simple to navigate. Simplicity is the key to all sophistication.

Links/Buttons
Menu
Gift Cards
Reservations
Take Out
Contact Us
Should not have
• Please, nothing generic looking… no cookie cutter look. Originality

```html
<!DOCTYPE html>
<html lang="en">
<head>
<meta charset="utf-8">
<title>Lumbra Ember Oven Kitchen</title>
<link rel="stylesheet" href="https://fonts.googleapis.com/css2?family=Montserrat:wght@400;500;600;700;800&family=Roboto+Slab:wght@400;500&family=Oswald:wght@500;600&family=Open+Sans:wght@400;600&display=swap">
<style>
:root{
  --black:#000;
  --ink:#0b0b0b;
  --panel:#1f1f1f;
  --panel-2:#262626;
  --line:#8a8a8a;
  --white:#fff;
  --muted:#b9b9b9;
  --red:#e2171f;
  --orange:#ff7b00;
  --ember:linear-gradient(90deg,var(--orange),var(--red));
}
*{box-sizing:border-box;margin:0;padding:0}
html,body{width:1200px;height:4107px;overflow:hidden;background:var(--black)}
body{position:relative;font-family:"Open Sans",Arial,sans-serif;color:var(--white)}
.abs{position:absolute}
.photo{position:absolute;display:block}
.center{text-align:center}
.slab{font-family:"Roboto Slab",Georgia,serif;letter-spacing:.14em;text-transform:uppercase}
.head{font-family:"Montserrat",Arial,sans-serif;font-weight:400;text-transform:uppercase;line-height:1}
.head b{font-weight:800}
.kicker{font-family:"Roboto Slab",Georgia,serif;color:var(--red);letter-spacing:.16em;text-transform:uppercase;font-size:15px}
.body-copy{font-size:13.5px;line-height:24px;color:var(--muted)}
.btn{position:absolute;display:flex;align-items:center;justify-content:center;font-family:"Montserrat",Arial,sans-serif;font-weight:700;text-transform:uppercase;font-size:11.5px;border-radius:30px;color:var(--white);text-decoration:none}
.btn-outline{border:2px solid var(--red)}
.btn-fill{background:var(--ember)}
.frame{position:absolute;border:2px solid #6e6e6e}
.cross{position:absolute;width:18px;height:18px}

/* nav */
.site-nav{position:absolute;left:0;top:0;width:1200px;height:80px;background:rgba(20,14,10,.72);z-index:5}
.nav-link{position:absolute;top:35px;font-family:"Montserrat",Arial,sans-serif;font-weight:600;font-size:11.5px;text-transform:uppercase;transform:translateX(-50%);white-space:nowrap}
.nav-link.active::after{content:"";position:absolute;left:-8px;right:-8px;top:40px;height:3px;background:var(--red)}
.brand{position:absolute;left:600px;top:14px;transform:translateX(-50%);text-align:center}
.brand-name{font-family:"Montserrat",Arial,sans-serif;font-weight:700;font-size:34px;line-height:34px;letter-spacing:.02em}
.brand-tag{font-family:"Roboto Slab",Georgia,serif;font-size:12px}

/* hero */
.hero-photo{left:0;top:0;width:1200px;height:720px;background:radial-gradient(ellipse at 55% 45%,#6b4a3a 0%,#3c2a22 35%,#1b1512 70%,#0d0a08 100%)}
.hero-box{position:absolute;left:252px;top:230px;width:700px;height:156px;border:2px solid rgba(255,255,255,.7);background:rgba(0,0,0,.32)}
.hero-arrow{position:absolute;top:298px;width:24px;height:36px}

/* welcome */
.welcome-ring{left:148px;top:692px;width:408px;height:408px;border-radius:50%;background:conic-gradient(from 200deg,var(--orange),var(--red),#5a0a0a,var(--orange));padding:14px}
.welcome-ring .inner{width:100%;height:100%;border-radius:50%;background:#222;padding:14px}
.welcome-ring .photo{position:relative;width:100%;height:100%;border-radius:50%;background:radial-gradient(circle at 45% 55%,#c0583a,#7a3524 55%,#3b2019)}

/* menu */
.menu-bg{left:0;top:1172px;width:1200px;height:374px;background:radial-gradient(ellipse at 20% 40%,#2a2a2a,#141414 60%,#0a0a0a)}
.menu-band{left:0;top:1546px;width:1200px;height:207px;background:#111}
.dish{position:absolute;top:1411px;height:291px;background:#1c1c1c;border-radius:0 56px 0 26px;overflow:hidden;text-align:center}
.dish .photo{position:relative;width:100%;height:191px}
.dish h3{font-family:"Oswald",Arial,sans-serif;font-weight:500;font-size:17px;text-transform:uppercase;margin-top:22px;letter-spacing:.02em}
.dish p{font-size:9px;line-height:14px;color:#9a9a9a;margin:6px auto 0;width:150px}
.dish.featured{top:1384px;height:341px;background:linear-gradient(180deg,var(--orange),var(--red) 60%,#b80f16);box-shadow:0 10px 30px rgba(0,0,0,.6)}
.dish.featured .photo{height:218px}
.dish.featured h3{font-size:26px;margin-top:20px}
.dish.featured p{color:#fff;font-size:11px;line-height:17px;width:170px}

/* gift */
.gift-bg{left:0;top:1753px;width:1200px;height:582px;background:#141414}
.voucher{position:absolute;left:143px;width:452px;height:212px;background:var(--panel);border-radius:60px 60px 60px 0;overflow:hidden}
.voucher .photo{left:0;top:0;width:216px;height:212px;border-radius:0 0 90px 0}
.badge{position:absolute;left:181px;top:71px;width:70px;height:70px;border-radius:50%;background:#111;border:4px solid var(--red);text-align:center;font-family:"Montserrat",Arial,sans-serif}
.badge strong{display:block;font-size:20px;line-height:20px;margin-top:14px;font-weight:700}
.badge span{font-size:7.5px;font-weight:700}
.voucher .v-kick{position:absolute;left:265px;top:53px;width:160px;text-align:center;font-family:"Roboto Slab",Georgia,serif;font-size:15px;color:var(--red);text-transform:uppercase}
.voucher h4{position:absolute;left:255px;top:70px;width:180px;text-align:center;font-family:"Montserrat",Arial,sans-serif;font-weight:700;font-size:28px}
.voucher .valid{position:absolute;left:255px;top:108px;width:180px;text-align:center;font-family:"Montserrat",Arial,sans-serif;font-size:9px;font-weight:600}
.voucher .fine{position:absolute;left:250px;top:126px;width:190px;text-align:center;font-size:8px;line-height:14px;color:#9a9a9a}

/* reservation */
.res-photo{left:0;top:2335px;width:1200px;height:426px;background:radial-gradient(ellipse at 50% 50%,#3a3028,#231d18 55%,#100d0b)}
.res-box{position:absolute;left:309px;top:2434px;width:584px;height:188px;border:2px solid rgba(255,255,255,.75)}

/* take out */
.takeout-bg{left:0;top:2761px;width:1200px;height:634px;background:radial-gradient(ellipse at 25% 50%,#1c1c1c,#060606 70%)}

/* contact */
.contact-bg{left:0;top:3395px;width:1200px;height:518px;background:linear-gradient(135deg,#2a2a2a,#1a1a1a 60%,#222)}
.contact-item{position:absolute;left:688px;width:420px;height:64px}
.contact-item .ring{position:absolute;left:0;top:0;width:62px;height:62px;border-radius:50%;border:2px solid var(--red);display:flex;align-items:center;justify-content:center}
.contact-item .label{position:absolute;left:88px;top:10px;font-size:13px;color:#cfcfcf}
.contact-item .value{position:absolute;left:88px;top:30px;font-size:15px;font-weight:600;font-family:"Open Sans",Arial,sans-serif}

/* footer */
.site-footer{left:0;top:3913px;width:1200px;height:194px;background:#000}
.foot-link{position:absolute;top:3969px;font-family:"Montserrat",Arial,sans-serif;font-weight:600;font-size:11.5px;text-transform:uppercase;transform:translateX(-50%);white-space:nowrap}
.social{position:absolute;top:4033px;width:34px;height:34px;border-radius:50%;background:var(--red)}
</style>
</head>
<body>

<!-- hero -->
<div class="photo hero-photo" role="img" aria-label="Close-up of a plated wood-oven dish with greens"></div>
<svg class="abs" style="left:0;top:560px" width="1200" height="160" viewBox="0 0 1200 160" aria-hidden="true">
  <path d="M0 150 C260 70 520 110 760 100 C960 92 1100 40 1200 20 L1200 160 L0 160 Z" fill="#000"/>
  <path d="M0 150 C260 70 520 110 760 100 C960 92 1100 40 1200 20" fill="none" stroke="#9a9a9a" stroke-width="6"/>
</svg>

<nav class="site-nav">
  <svg class="cross" style="left:168px;top:17px;width:14px;height:14px" viewBox="0 0 14 14" aria-hidden="true"><path d="M2 2L12 12M12 2L2 12" stroke="#fff" stroke-width="1.6"/></svg>
  <a class="nav-link active" style="left:177px">About Us</a>
  <a class="nav-link" style="left:276px">Menu</a>
  <a class="nav-link" style="left:388px">Reservation</a>
  <div class="brand"><div class="brand-name">LUMBRA</div><div class="brand-tag">Ember Oven Kitchen</div></div>
  <a class="nav-link" style="left:808px">Takeout</a>
  <a class="nav-link" style="left:925px">Gift Cards</a>
  <a class="nav-link" style="left:1039px">Contact</a>
</nav>

<svg class="hero-arrow" style="left:34px" viewBox="0 0 24 36" aria-hidden="true"><path d="M18 4L6 18L18 32" fill="none" stroke="#fff" stroke-width="4"/></svg>
<svg class="hero-arrow" style="left:1138px" viewBox="0 0 24 36" aria-hidden="true"><path d="M6 4L18 18L6 32" fill="none" stroke="#fff" stroke-width="4"/></svg>

<section class="hero-box">
  <div class="slab center" style="margin-top:26px;font-size:24px">Welcome to Lumbra</div>
  <h1 class="center" style="font-family:'Montserrat',Arial,sans-serif;font-weight:800;font-size:50px;line-height:54px;text-transform:uppercase;letter-spacing:.02em">Ember Oven Kitchen</h1>
</section>
<a class="btn btn-fill" style="left:489px;top:364px;width:220px;height:46px;font-size:13px">Book Reservation</a>

<!-- welcome -->
<div class="abs welcome-ring"><div class="inner"><div class="photo" role="img" aria-label="Wood-fired pizzas on a counter"></div></div></div>
<div class="frame" style="left:486px;top:733px;width:590px;height:346px;border-left:none"></div>
<svg class="cross" style="left:608px;top:780px" viewBox="0 0 18 18" aria-hidden="true"><path d="M3 3L15 15M15 3L3 15" stroke="#fff" stroke-width="1.6"/></svg>
<h2 class="head abs" style="left:602px;top:804px;font-size:32px">Welcome to <b>Lumbra</b></h2>
<div class="abs body-copy" style="left:602px;top:850px;width:450px;color:#c9c9c9">
  <p>Sed ut perspiciatis unde omnis iste natus error sit voluptatem accusan-tium doloremque laudantium, totam rem .</p>
  <p>aperiam, eaque ipsa quae ab illo inventore veritatis et quasi architecto beatae vitae dicta sunt explicabo. Nemo enim ipsam voluptatem quia voluptas sit aspernatur aut odit aut fugit, sed quia</p>
</div>
<a class="btn btn-outline" style="left:607px;top:992px;width:155px;height:40px">View Our Menu</a>

<!-- menu -->
<div class="photo menu-bg" role="img" aria-label="Dark textured food backdrop"></div>
<div class="abs menu-band"></div>
<div class="kicker abs center" style="left:0;top:1222px;width:1200px">Taste</div>
<h2 class="head abs center" style="left:0;top:1248px;width:1200px;font-size:36px">Our <b>Menu</b></h2>
<p class="abs center" style="left:300px;top:1284px;width:600px;font-size:15px;line-height:27px;color:#e6e6e6">Sed ut perspiciatis unde omnis iste natus error sit avoluptatem accusantium dolor-emque laudantium, totam rem .aperiam.</p>

<article class="dish" style="left:80px;width:199px"><div class="photo" role="img" aria-label="Wood-fired pizzas" style="background:linear-gradient(160deg,#5a4a3c,#8c4a2c 60%,#3a2a20)"></div><h3>Wodd Fired Pizza</h3><p>Sed ut perspiciatis unde omnis iste Sed ut perspiciatis</p></article>
<article class="dish" style="left:287px;width:191px"><div class="photo" role="img" aria-label="Burger with avocado" style="background:linear-gradient(160deg,#6a5648,#9a6a3a 55%,#3d4a2a)"></div><h3 style="margin-top:30px">Special Burger</h3><p>Sed ut perspiciatis unde omnis iste Sed ut perspiciatis</p></article>
<article class="dish featured" style="left:481px;width:239px;border-radius:0 60px 0 30px"><div class="photo" role="img" aria-label="Fried chicken burger" style="background:linear-gradient(170deg,#5b5a3a,#c46a2a 55%,#7a3020)"></div><h3>Fried Burger</h3><p>Sed ut perspiciatis unde omnis iste Sed ut perspiciatis</p></article>
<article class="dish" style="left:720px;width:193px"><div class="photo" role="img" aria-label="Pasta main dish" style="background:linear-gradient(160deg,#8a8a80,#a69a70 50%,#4a4a3a)"></div><h3 style="margin-top:30px">Mains &amp; Pasta</h3><p>Sed ut perspiciatis unde omnis iste Sed ut perspiciatis</p></article>
<article class="dish" style="left:918px;width:198px"><div class="photo" role="img" aria-label="Grilled sandwich with salad" style="background:linear-gradient(160deg,#a09080,#6a4a30 50%,#2a3a1a)"></div><h3 style="margin-top:34px">Special Sandwich</h3><p>Sed ut perspiciatis unde omnis iste Sed ut perspiciatis</p></article>

<!-- gift cards -->
<div class="abs gift-bg"></div>
<div class="frame" style="left:574px;top:1808px;width:513px;height:417px;border-left:none"></div>
<div class="voucher" style="top:1800px">
  <div class="photo" role="img" aria-label="Bowls of dips and spreads" style="background:radial-gradient(circle at 40% 50%,#a5703a,#6a6a3a 50%,#2a2a22)"></div>
  <div class="badge"><strong>35%</strong><span>DISCOUNT</span></div>
  <div class="v-kick">Main Meal</div>
  <h4>VOUCHER</h4>
  <div class="valid">VALID 20 AUG 2021</div>
  <div class="fine">Sed ut perspiciatis unde omnis iste natus error sit avoluptatem accusantium</div>
</div>
<div class="voucher" style="top:2028px">
  <div class="photo" role="img" aria-label="Fired pizza on a board" style="background:radial-gradient(circle at 45% 55%,#c0583a,#7a3524 55%,#3b2019)"></div>
  <div class="badge"><strong>25%</strong><span>DISCOUNT</span></div>
  <div class="v-kick" style="color:var(--orange)">Fired Pizza</div>
  <h4>VOUCHER</h4>
  <div class="valid">VALID 20 AUG 2021</div>
  <div class="fine">Sed ut perspiciatis unde omnis iste natus error sit avoluptatem accusantium</div>
</div>
<div class="kicker abs" style="left:660px;top:1911px;font-size:13px">Offer &amp; Discounts</div>
<h2 class="head abs" style="left:660px;top:1936px;font-size:38px">Gift <b>Cards</b></h2>
<p class="abs body-copy" style="left:660px;top:1990px;width:400px;color:#a9a9a9">Sed ut perspiciatis unde omnis iste natus error sit avo-luptatem accusantium Sed ut perspiciatis unde omnis iste natus error sit avoluptatem accusantium</p>
<a class="btn btn-outline" style="left:658px;top:2082px;width:155px;height:40px;font-size:10px">View More Cards</a>

<!-- reservation -->
<div class="photo res-photo" role="img" aria-label="Tacos with onion and cilantro on a dark plate"></div>
<div class="res-box"></div>
<svg class="cross" style="left:592px;top:2424px;background:transparent" viewBox="0 0 18 18" aria-hidden="true"><path d="M3 3L15 15M15 3L3 15" stroke="#fff" stroke-width="1.6"/></svg>
<div class="slab abs center" style="left:309px;top:2461px;width:584px;font-size:19px">Enjoy Your Meal</div>
<h2 class="head abs center" style="left:309px;top:2489px;width:584px;font-size:38px">Book <b>Reservation</b></h2>
<p class="abs center" style="left:400px;top:2534px;width:402px;font-size:14px;line-height:21px;color:#e0e0e0">Sed ut perspiciatis unde omnis iste natus error sit avo-luptatem accusantium doloremque</p>
<a class="btn btn-fill" style="left:526px;top:2607px;width:151px;height:36px;font-size:11px">Book Now</a>

<!-- take out -->
<div class="photo takeout-bg" role="img" aria-label="Dark smoky backdrop"></div>
<div class="frame" style="left:108px;top:2893px;width:485px;height:418px;border-right:none"></div>
<div class="kicker abs" style="left:180px;top:2993px;font-size:14px">Enjoy Your Meal</div>
<h2 class="head abs" style="left:180px;top:3016px;font-size:38px">Take <b style="font-weight:500">Out</b></h2>
<p class="abs body-copy" style="left:180px;top:3070px;width:370px;color:#a9a9a9">Sed ut perspiciatis unde omnis iste natus error sit avo-luptatem accusantium Sed ut perspiciatis unde omnis iste natus error sit avoluptatem accusantium</p>
<a class="btn btn-outline" style="left:188px;top:3170px;width:155px;height:40px">Book Now</a>
<div class="photo" role="img" aria-label="Table of dips and flatbreads" style="left:579px;top:2872px;width:430px;height:396px;background:linear-gradient(150deg,#4a4a44,#8a6a44 50%,#2a2a22)"></div>
<div class="photo" role="img" aria-label="The kitchen team in front of the oven" style="left:653px;top:2962px;width:423px;height:345px;background:linear-gradient(160deg,#6a5a4a,#3a302a 55%,#181412)"></div>
<div class="abs" style="left:622px;top:2933px;width:419px;height:405px;border:4px solid var(--red)"></div>

<!-- contact -->
<div class="abs contact-bg"></div>
<svg class="abs" style="left:0;top:3395px" width="600" height="518" viewBox="0 0 600 518" role="img" aria-label="Tacos with red cabbage and grilled meat">
  <defs><linearGradient id="taco" x1="0" y1="0" x2="1" y2="1"><stop offset="0" stop-color="#6a5a3a"/><stop offset=".5" stop-color="#8a3a4a"/><stop offset="1" stop-color="#3a2a1a"/></linearGradient></defs>
  <path d="M0 0 H470 C560 130 590 330 490 518 H0 Z" fill="url(#taco)"/>
  <path d="M470 0 C560 130 590 330 490 518" fill="none" stroke="var(--red)" stroke-width="5"/>
</svg>
<div class="kicker abs" style="left:684px;top:3489px;font-size:14px">Contact Us</div>
<svg class="cross" style="left:797px;top:3489px;width:15px;height:15px" viewBox="0 0 18 18" aria-hidden="true"><path d="M3 3L15 15M15 3L3 15" stroke="#fff" stroke-width="1.8"/></svg>
<h2 class="head abs" style="left:682px;top:3513px;font-size:37px">Get in Touch</h2>

<div class="contact-item" style="top:3586px">
  <div class="ring"><svg width="24" height="24" viewBox="0 0 24 24" aria-hidden="true"><path d="M6 3l3 4-2 2c1 3 3 5 6 6l2-2 4 3-2 3C10 19 5 14 3 5z" fill="none" stroke="#fff" stroke-width="1.5"/></svg></div>
  <div class="label">Phone Number</div><div class="value">555-014-2290</div>
</div>
<div class="contact-item" style="top:3658px">
  <div class="ring"><svg width="24" height="24" viewBox="0 0 24 24" aria-hidden="true"><path d="M21 3L3 11l7 3 3 7z" fill="#fff"/></svg></div>
  <div class="label">Email enquiry</div><div class="value">enquiry@lumbrabexwell.example</div>
</div>
<div class="contact-item" style="top:3734px">
  <div class="ring"><svg width="24" height="24" viewBox="0 0 24 24" aria-hidden="true"><path d="M12 22s7-8 7-13a7 7 0 0 0-14 0c0 5 7 13 7 13z" fill="#fff"/><circle cx="12" cy="9" r="2.5" fill="#222"/></svg></div>
  <div class="label">Location</div><div class="value">1207 Alder Row, Bexwell</div>
</div>

<!-- footer -->
<footer class="abs site-footer"></footer>
<a class="foot-link" style="left:247px">Home</a>
<a class="foot-link" style="left:350px">About Us</a>
<a class="foot-link" style="left:452px">Menu</a>
<a class="foot-link" style="left:567px">Reservation</a>
<a class="foot-link" style="left:694px">Takeout</a>
<a class="foot-link" style="left:812px">Gift Cards</a>
<a class="foot-link" style="left:931px">Contact</a>
<p class="abs center" style="left:0;top:3999px;width:1200px;font-family:'Montserrat',Arial,sans-serif;font-size:11px;color:#ddd">Copyright © 2021 Lumbra All Right Reserved</p>
<a class="social" style="left:538px" aria-label="Social link"></a>
<a class="social" style="left:578px" aria-label="Social link"></a>
<a class="social" style="left:617px" aria-label="Social link"></a>

</body>
</html>
```